My project benefits Military, First Responders, Police, Fire, and Educators.

Contact Information for Business Card

2 Sided appointment card. Visual side will have my head shot with "Brisk Lantern" in a bold graffic/text. I am picturing maybe the headshot applied to a filter that has a matrix effect where the picture is made up of data/numbers flowing vertically through the photo. I am of course open to other concepts as well. Side two will have contact info presented in an attractive visual complimenting the front.

```html
<!DOCTYPE html>
<html lang="en">
<head>
<meta charset="utf-8">
<title>Brisk Lantern – Appointment Card</title>
<link rel="stylesheet" href="https://fonts.googleapis.com/css2?family=Open+Sans:wght@400;600;700&display=swap">
<style>
  :root {
    --stage: #e9e7e4;
    --card-dark: #121212;
    --card-light: #ffffff;
    --brand-green: #1fa77a;
    --accent-green: #2bbf8b;
    --ink-navy: #1d2b5a;
    --ink-grey: #3a3a3a;
    --ring-grey: #707070;
    --text-light: #f2f2f2;
  }
  * { box-sizing: border-box; margin: 0; padding: 0; }
  html, body {
    width: 1200px; height: 900px; overflow: hidden;
    background: var(--stage);
    font-family: "Open Sans", Arial, sans-serif;
  }
  .stage {
    position: relative; width: 1200px; height: 900px;
    display: flex; align-items: center; justify-content: center; gap: 40px;
  }
  .card {
    position: relative; width: 540px; height: 310px; overflow: hidden;
    box-shadow: 0 6px 18px rgba(0,0,0,.18);
  }

  /* Front: headshot side */
  .card--front { background: var(--card-dark); }
  .headshot {
    position: absolute; left: 0; top: 0; width: 300px; height: 310px;
    background:
      radial-gradient(ellipse 55% 45% at 45% 38%, #c98e6e 0%, #8a5a43 45%, transparent 75%),
      linear-gradient(180deg, #1a1a1a 0%, #1a1a1a 55%, #1c2a4a 70%, #14203c 100%);
  }
  .divider {
    position: absolute; left: 292px; top: 90px; width: 1px; height: 120px;
    background: var(--accent-green);
  }
  .profile { position: absolute; left: 318px; top: 84px; color: var(--text-light); }
  .profile__name { color: var(--accent-green); font-weight: 700; font-size: 19px; line-height: 1.1; }
  .profile__role { font-size: 14px; margin-top: 2px; }
  .contacts { list-style: none; margin-top: 28px; font-size: 14px; }
  .contacts li { display: flex; align-items: center; gap: 10px; line-height: 21px; }
  .contacts svg { width: 12px; height: 12px; fill: var(--accent-green); flex: none; }

  /* Back: appointment side */
  .card--back { background: var(--card-light); color: var(--ink-grey); }
  .brand {
    position: absolute; top: 22px; left: 0; right: 0;
    display: flex; flex-direction: column; align-items: center; gap: 8px;
  }
  .brand__mark {
    width: 62px; height: 62px; border-radius: 50%;
    border: 6px solid var(--ring-grey);
  }
  .brand__name {
    color: var(--brand-green); font-weight: 400; font-size: 24px;
    letter-spacing: .5px; text-transform: uppercase;
  }
  .appointment__title {
    position: absolute; top: 138px; left: 0; right: 0; text-align: center;
    color: var(--brand-green); font-weight: 700; font-size: 20px;
  }
  .field { position: absolute; display: flex; align-items: flex-end; font-size: 13px; gap: 8px; }
  .field__line { flex: 1; height: 1px; background: var(--accent-green); margin-bottom: 4px; }
  .field--name { left: 40px; right: 40px; top: 188px; }
  .field--date { left: 40px; width: 260px; top: 222px; }
  .field--time { left: 320px; right: 40px; top: 222px; }
  .notice {
    position: absolute; top: 262px; left: 0; right: 0; text-align: center;
    color: var(--ink-navy); font-weight: 700; font-size: 14px;
  }
</style>
</head>
<body>
<main class="stage">
  <section class="card card--front">
    <div class="headshot" role="img" aria-label="Headshot of Daniel Reeve in a navy suit and striped tie"></div>
    <div class="divider"></div>
    <div class="profile">
      <p class="profile__name">Daniel Reeve</p>
      <p class="profile__role">Managing Director</p>
      <ul class="contacts">
        <li><svg viewBox="0 0 24 24" aria-hidden="true"><path d="M6.6 10.8a15.1 15.1 0 0 0 6.6 6.6l2.2-2.2a1 1 0 0 1 1-.25 11.4 11.4 0 0 0 3.6.57 1 1 0 0 1 1 1V20a1 1 0 0 1-1 1A17 17 0 0 1 3 4a1 1 0 0 1 1-1h3.5a1 1 0 0 1 1 1c0 1.25.2 2.45.57 3.57a1 1 0 0 1-.25 1z"/></svg>044-555 018 273</li>
        <li><svg viewBox="0 0 24 24" aria-hidden="true"><path d="M2 5h20v14H2z M2 5l10 8 10-8" fill="var(--accent-green)"/><path d="M3 6l9 7 9-7" stroke="#121212" stroke-width="2" fill="none"/></svg>hello@brisklantern.com</li>
        <li><svg viewBox="0 0 24 24" aria-hidden="true"><circle cx="12" cy="12" r="10"/><path d="M2 12h20M12 2c3 3 3 17 0 20M12 2c-3 3-3 17 0 20" stroke="#121212" stroke-width="1.6" fill="none"/></svg>www.brisklantern.com</li>
      </ul>
    </div>
  </section>

  <section class="card card--back">
    <div class="brand">
      <span class="brand__mark" aria-hidden="true"></span>
      <span class="brand__name">Brisk Lantern</span>
    </div>
    <h2 class="appointment__title">Your Next Appointment is</h2>
    <div class="field field--name"><span>Name :</span><span class="field__line"></span></div>
    <div class="field field--date"><span>Date :</span><span class="field__line"></span></div>
    <div class="field field--time"><span>Time:</span><span class="field__line"></span></div>
    <p class="notice">If unable to keep appointment, kindly give 24hrs notice.</p>
  </section>
</main>
</body>
</html>
```